Koru Glaze Sauce food label

i have an old label that is provided. i would like to keep the hand drawn ninja logo and the Japanese writing. This needs to be printed on a 10oz woozy bottle that is at most 3.5" height and 6" length.

Please add a place for social media and the website, www.korubrightglaze.com.

Please delete the part with the address, recipe suggestions, and part about the exotic blend.

the teriyaki sauce will be sold locally in the SF bay and farmers markets.

everything else is up for a new design but i would like to stick to a Japanese theme and colors. We are looking for an updated design that will still be a semi premium product.

Target Market(s)

farmers markets and local markets in SF bay area, and eventually online

Industry/Entity Type

food and sauces

Font styles to use
Other font styles liked:
• anything easy to read.

Colors
EB3D1F
EC4F4E
F09395
F8D3D4
FCEDEE

Requirements
Must have
• must have the original hand drawn ninja and japanese writing. both can be recolored, resized.
Should not have
• try to keep with the Japanese color theme of white, red, black, and possibly gold/silver

```html
<!DOCTYPE html>
<html lang="en">
<head>
<meta charset="utf-8">
<title>Koru Glaze Sauce – Label</title>
<link rel="stylesheet" href="https://fonts.googleapis.com/css2?family=Cinzel:wght@700;800;900&family=Oswald:wght@500&display=swap">
<style>
  :root {
    --page: #ffffff;
    --label-paper: #ece2cb;
    --label-paper-light: #f4ecd9;
    --rule: #2a2623;
    --brand-red: #c81c22;
    --sun-red: #cc2127;
    --ink: #141414;
  }
  html, body {
    margin: 0;
    padding: 0;
    width: 1200px;
    height: 1180px;
    overflow: hidden;
    background: var(--page);
  }
  .canvas {
    position: relative;
    width: 1200px;
    height: 1180px;
  }
  .label {
    position: absolute;
    left: 200px;
    top: 26px;
    width: 800px;
    height: 1128px;
    overflow: hidden;
    background: radial-gradient(circle at 50% 46%, var(--label-paper-light) 0%, var(--label-paper) 70%);
  }
  .label-rule {
    position: absolute;
    left: 0;
    width: 100%;
    height: 2px;
    background: var(--rule);
  }
  .label-rule.top { top: 30px; }
  .label-rule.bottom { top: 1100px; }
  .brand-name {
    position: absolute;
    top: 70px;
    left: 0;
    width: 100%;
    margin: 0;
    text-align: center;
    font-family: "Cinzel", serif;
    font-weight: 800;
    font-size: 236px;
    line-height: 1;
    letter-spacing: 0;
    color: var(--brand-red);
    white-space: nowrap;
  }
  .emblem {
    position: absolute;
    left: 0;
    top: 0;
    width: 800px;
    height: 700px;
  }
  .product-name {
    position: absolute;
    top: 700px;
    left: 0;
    width: 100%;
    margin: 0;
    text-align: center;
    font-family: "Cinzel", serif;
    font-weight: 700;
    color: var(--ink);
    line-height: 1;
  }
  .product-name .line {
    display: block;
    font-size: 120px;
    letter-spacing: 3px;
  }
  .product-name .line + .line { margin-top: 6px; }
  .net-weight {
    position: absolute;
    top: 968px;
    left: 0;
    width: 100%;
    margin: 0;
    text-align: center;
    font-family: "Oswald", sans-serif;
    font-weight: 500;
    font-size: 34px;
    line-height: 1;
    color: var(--ink);
  }
  .contact-row {
    position: absolute;
    top: 1030px;
    left: 0;
    width: 100%;
    display: flex;
    justify-content: center;
    align-items: center;
    gap: 22px;
  }
  .social-icons {
    display: flex;
    gap: 10px;
  }
  .social-icon {
    width: 30px;
    height: 30px;
    border-radius: 50%;
    background: var(--brand-red);
  }
  .website {
    margin: 0;
    font-family: "Oswald", sans-serif;
    font-weight: 500;
    font-size: 28px;
    line-height: 1;
    letter-spacing: 1px;
    color: var(--ink);
  }
</style>
</head>
<body>
  <div class="canvas">
    <section class="label">
      <div class="label-rule top"></div>

      <h1 class="brand-name">KORU</h1>

      <svg class="emblem" viewBox="0 0 800 700" xmlns="http://www.w3.org/2000/svg">
        <defs>
          <clipPath id="sun-clip">
            <rect x="0" y="0" width="800" height="686"/>
          </clipPath>
        </defs>
        <g role="img" aria-label="Hand-drawn leaping ninja with two swords in front of a red rising sun">
          <circle cx="398" cy="516" r="200" fill="var(--sun-red)" clip-path="url(#sun-clip)"/>
        </g>
        <rect role="img" aria-label="Japanese brush writing reading ninja" x="628" y="420" width="96" height="192" rx="6" fill="var(--ink)" opacity="0.82"/>
      </svg>

      <h2 class="product-name">
        <span class="line">GLAZE</span>
        <span class="line">SAUCE</span>
      </h2>

      <p class="net-weight">NET WT.: 10oz</p>

      <div class="contact-row">
        <div class="social-icons" role="img" aria-label="Social media links">
          <span class="social-icon"></span>
          <span class="social-icon"></span>
          <span class="social-icon"></span>
        </div>
        <p class="website">www.korubrightglaze.com</p>
      </div>

      <div class="label-rule bottom"></div>
    </section>
  </div>
</body>
</html>
```